Alliance Holiday Card thanking supporters

- Use a vertical (not horizontal) layout.

- On the front, use a few dozen small boxes (no smaller than .2x.2, no bigger than .3x.3) with pictures of different principals. On top of the boxes, a large map of Chicago, with dots for every principal we’re directly supporting through KRM, PLCs, coaching, BWT, etc. this year. Data for map will be sent on a different day.

- On the inside: Thanks to you, The Harrowgate Civic Alliance directly supports XXX public school principals across Chicago.

On behalf of our city’s best educators,
happy holidays!

We look forward to our continued partnership in the year ahead.

Target Market(s)

Funders and supporters

Industry/Entity Type

Education

Font styles to use
Sans Serif

Requirements
Must have
• Picture of principals and map
Nice to have
• dots on map
Should not have
• Our logo colors are red, gray and white.

```html
<!DOCTYPE html>
<html lang="en">
<head>
<meta charset="utf-8">
<title>Harrowgate Civic Alliance Holiday Card</title>
<link rel="stylesheet" href="https://fonts.googleapis.com/css2?family=EB+Garamond:wght@400;500&family=Oswald:wght@500&display=swap">
<style>
  :root {
    --backdrop: #efefef;
    --paper: #ffffff;
    --map-light: #c9c9c9;
    --map-dark: #8c8c8c;
    --brand-red: #b0203a;
    --dot-orange: #e0552a;
    --photo-tone: #7d6f68;
    --ink-gray: #6b6b6b;
    --ink-soft: #9a9a9a;
  }
  * { margin: 0; padding: 0; box-sizing: border-box; }
  html, body { width: 1200px; height: 906px; overflow: hidden; }
  body { background: var(--backdrop); position: relative; }

  .card { position: absolute; top: 22px; height: 860px; background: var(--paper); }
  .card-front { left: 45px; width: 551px; overflow: hidden; }
  .card-inside { left: 624px; width: 554px; }

  .map-area {
    position: absolute; inset: 0;
    background: radial-gradient(ellipse at 30% 55%, var(--map-light) 0%, var(--map-dark) 85%);
  }
  .map-markers { position: absolute; inset: 0; }
  .dot { fill: var(--dot-orange); }
  .pin-body { fill: var(--brand-red); }
  .pin-photo { fill: var(--photo-tone); }

  .front-title {
    position: absolute; left: 52px; bottom: 52px;
    font-family: "EB Garamond", serif; font-variant: small-caps;
    font-size: 30px; letter-spacing: 1px; color: var(--paper);
  }

  .inside-message {
    position: absolute; left: 0; right: 0; top: 362px;
    text-align: center; font-family: "EB Garamond", serif;
  }
  .intro { font-size: 14px; line-height: 21px; color: var(--ink-gray); }
  .divider { width: 40px; height: 1px; background: var(--ink-soft); margin: 9px auto 14px; }
  .dedication {
    font-family: "Oswald", sans-serif; font-weight: 500;
    font-size: 17px; letter-spacing: .4px; color: var(--ink-gray);
  }
  .greeting { font-size: 46px; line-height: 50px; color: var(--brand-red); }
  .closing { margin-top: 4px; font-size: 15px; color: var(--ink-soft); }
</style>
</head>
<body>
  <section class="card card-front">
    <div class="map-area" role="img" aria-label="Map of Chicago showing supported principals"></div>
    <svg class="map-markers" viewBox="0 0 551 860" width="551" height="860">
      <defs>
        <g id="pin">
          <path class="pin-body" d="M-23 10 A25 25 0 1 1 23 10 L0 40 Z"/>
          <circle class="pin-photo" r="19"/>
        </g>
      </defs>
      <g class="dots">
        <circle class="dot" cx="45" cy="80" r="5"/><circle class="dot" cx="60" cy="130" r="5"/>
        <circle class="dot" cx="132" cy="98" r="5"/><circle class="dot" cx="174" cy="178" r="5"/>
        <circle class="dot" cx="222" cy="58" r="5"/><circle class="dot" cx="343" cy="38" r="5"/>
        <circle class="dot" cx="294" cy="112" r="5"/><circle class="dot" cx="294" cy="168" r="5"/>
        <circle class="dot" cx="369" cy="180" r="5"/><circle class="dot" cx="235" cy="232" r="5"/>
        <circle class="dot" cx="324" cy="228" r="5"/><circle class="dot" cx="388" cy="230" r="5"/>
        <circle class="dot" cx="294" cy="318" r="5"/><circle class="dot" cx="363" cy="322" r="5"/>
        <circle class="dot" cx="415" cy="322" r="5"/><circle class="dot" cx="369" cy="370" r="5"/>
        <circle class="dot" cx="420" cy="378" r="5"/><circle class="dot" cx="306" cy="412" r="5"/>
        <circle class="dot" cx="396" cy="432" r="5"/><circle class="dot" cx="298" cy="454" r="5"/>
        <circle class="dot" cx="285" cy="507" r="5"/><circle class="dot" cx="426" cy="498" r="5"/>
        <circle class="dot" cx="448" cy="510" r="5"/><circle class="dot" cx="208" cy="540" r="5"/>
        <circle class="dot" cx="360" cy="544" r="5"/><circle class="dot" cx="483" cy="607" r="5"/>
        <circle class="dot" cx="288" cy="618" r="5"/><circle class="dot" cx="373" cy="640" r="5"/>
        <circle class="dot" cx="438" cy="667" r="5"/><circle class="dot" cx="348" cy="687" r="5"/>
        <circle class="dot" cx="303" cy="723" r="5"/><circle class="dot" cx="502" cy="723" r="5"/>
        <circle class="dot" cx="352" cy="747" r="5"/><circle class="dot" cx="432" cy="739" r="5"/>
        <circle class="dot" cx="459" cy="817" r="5"/><circle class="dot" cx="423" cy="787" r="5"/>
      </g>
      <g class="pins" role="img" aria-label="Portraits of supported principals">
        <use href="#pin" x="90" y="40"/><use href="#pin" x="405" y="35"/>
        <use href="#pin" x="245" y="112"/><use href="#pin" x="432" y="172"/>
        <use href="#pin" x="172" y="232"/><use href="#pin" x="352" y="255"/>
        <use href="#pin" x="475" y="301"/><use href="#pin" x="235" y="340"/>
        <use href="#pin" x="457" y="430"/><use href="#pin" x="235" y="450"/>
        <use href="#pin" x="144" y="540"/><use href="#pin" x="502" y="547"/>
        <use href="#pin" x="328" y="595"/><use href="#pin" x="247" y="727"/>
        <use href="#pin" x="505" y="760"/>
      </g>
    </svg>
    <h1 class="front-title">Thank You</h1>
  </section>

  <section class="card card-inside">
    <div class="inside-message">
      <p class="intro">The Harrowgate Civic Alliance directly supports XXX public school<br>principals across Chicago.</p>
      <div class="divider"></div>
      <p class="dedication">ON BEHALF OF OUR CITY’S BEST EDUCATORS,</p>
      <p class="greeting">Happy Holidays!</p>
      <p class="closing">We look forward to your continued partnership in the year ahead.</p>
    </div>
  </section>
</body>
</html>
```